Need Instructors for martial arts school - special flyers to help

We are a kung fu and tai chi martial arts school and we need to appeal to a certain demographic - 16-30, driven, fit, personable - who can join our team of instructors to help grow our school. We envisage this flyer as as roughly between A6 and A7 in size. The kind of thing we can hand to some one we meet and they can easily stick it in a pocket but not so small it gets lost like a business card. We are a professional and serious organisation so don't want to go too dramatic or cheesy to get attention but the design needs to capture the attention of the reader quickly and keep them engaged. Martial arts has quite a bit of material to use for this purpose. NOTE: we are not Karate or Tae Kwon Do - the difference matters. We will upload our current logo and the text we want to use is this for the front:
"Challenge Yourself...
Teaching is the highest form of learning. Be a part of a professional, dedicated team, delivering the highest level Kung Fu...
Copper Wren Martial Arts"
On the back side it should say:
"Seeking martial arts instructors!
We train in one of the world's most effective martial art systems, Choy Li Fut Kung Fu. As an instructor, you will teach both beginner and intermediate level Kung Fu skills to adults and children at Copper Wren Martial Arts, Brisbane's premier martial arts school.
As an instructor, you will:
- Teach fundamentals to children and adults of all ages and abilities
- Progress student's martial arts and life skills
- Deliver fun and engaging classes
- Develop and grow your martial arts skills at an advanced level and pace
In return, you will receive your training tuition, which includes our high level instructor training program, until qualified and then a weekly one one on one with our very own Sifu, as well as one hour training sessions, twice a week , with our team.
At CWMA our motto is "Challenge yourself... for life!"
Contact us on 0491 570 183 to discuss your interest and suitability - ask for Sifu Rory."
There are two fonts we are liking right now for our designs, Merienda One and Red Rose from Google Fonts.
We basically need this to be cool enough to keep someone's attention and not have them throw it away before they have read it.
Info about us on copperwrenexample.com.au

```html
<!DOCTYPE html>
<html lang="en">
<head>
<meta charset="utf-8">
<title>Copper Wren Martial Arts – Instructor Flyer</title>
<link rel="stylesheet" href="https://fonts.googleapis.com/css2?family=Montserrat:wght@600;700;800;900&family=Merienda:wght@400;700&family=Red+Rose:wght@400;500&display=swap">
<style>
  :root {
    --red: #e2202a;
    --red-deep: #a01d24;
    --charcoal: #332b2b;
    --charcoal-soft: #4a4242;
    --white: #ffffff;
    --paper: #ececec;
    --ink: #2b2626;
    --body-font: "Montserrat", Arial, sans-serif;
    --script-font: "Merienda", cursive;
    --brand-font: "Red Rose", sans-serif;
  }
  * { box-sizing: border-box; margin: 0; padding: 0; }
  html, body { width: 1200px; height: 908px; overflow: hidden; background: var(--white); }
  .canvas { position: relative; width: 1200px; height: 908px; }

  .flyer {
    position: absolute;
    width: 472px;
    height: 664px;
    overflow: hidden;
    box-shadow: 8px 10px 18px rgba(0,0,0,0.22);
  }

  /* Front */
  .flyer--front {
    left: 79px; top: 79px;
    background:
      radial-gradient(ellipse 70% 45% at 35% 100%, rgba(226,32,42,0.85), rgba(226,32,42,0) 75%),
      linear-gradient(135deg, var(--red) 0%, var(--red-deep) 35%, var(--charcoal) 70%, var(--charcoal) 100%);
    font-family: var(--body-font);
    color: var(--white);
  }
  .front__headline { position: absolute; left: 0; top: 22px; width: 100%; }
  .front__challenge {
    position: absolute; left: 71px; top: 0;
    font-size: 67px; font-weight: 800; letter-spacing: -0.5px; line-height: 1;
  }
  .front__yourself {
    position: absolute; left: 167px; top: 72px;
    font-size: 41px; font-weight: 800; line-height: 1;
  }
  .front__photo {
    position: absolute; left: 0; top: 132px; width: 460px; height: 330px;
    background: radial-gradient(ellipse 55% 50% at 40% 50%, rgba(150,140,135,0.55), rgba(150,140,135,0) 80%);
  }
  .front__pitch {
    position: absolute; right: 31px; top: 284px; width: 260px;
    text-align: right; font-size: 15px; font-weight: 700; line-height: 22px;
  }
  .front__seal {
    position: absolute; left: 263px; top: 482px; width: 126px; height: 126px;
    border: 2px solid var(--white); border-radius: 50%;
    background: var(--charcoal);
  }
  .front__brand {
    position: absolute; right: 37px; top: 620px;
    font-size: 17px; font-weight: 800; white-space: nowrap;
  }

  /* Back */
  .flyer--back { left: 625px; top: 179px; background: var(--paper); font-family: var(--body-font); }
  .back__bands { position: absolute; inset: 0; }
  .back__title {
    position: absolute; left: 35px; top: 18px;
    font-family: var(--script-font); font-weight: 700; font-style: normal;
    font-size: 37px; line-height: 44px; color: var(--white); letter-spacing: 0.5px;
  }
  .back__copy {
    position: absolute; left: 37px; top: 168px; width: 410px;
    color: var(--white); font-size: 13.6px; font-weight: 700; line-height: 19.8px;
  }
  .back__copy p + p, .back__copy p + .duties, .back__copy .duties + p { margin-top: 9px; }
  .duties { list-style: none; }
  .duties li { position: relative; padding-left: 21px; }
  .duties li::before { content: "-"; position: absolute; left: 0; }
  .back__contact { position: absolute; left: 34px; top: 584px; color: var(--red); font-weight: 700; }
  .back__contact-note { font-size: 8.6px; line-height: 11px; }
  .back__phone { font-size: 20px; font-weight: 800; margin-top: 4px; letter-spacing: 0.3px; }
  .back__brand { position: absolute; left: 200px; top: 578px; }
  .back__brand-name {
    font-family: var(--brand-font); font-weight: 400; color: var(--ink);
    font-size: 19.5px; line-height: 20px;
  }
  .back__motto {
    font-family: var(--script-font); color: var(--red);
    font-size: 11px; margin-top: 4px; white-space: nowrap;
  }
  .back__seal {
    position: absolute; left: 357px; top: 569px; width: 80px; height: 80px;
    border: 1.5px solid var(--ink); border-radius: 50%;
  }
</style>
</head>
<body>
<main class="canvas">

  <section class="flyer flyer--front" aria-label="Flyer front">
    <h1 class="front__headline">
      <span class="front__challenge">Challenge</span>
      <span class="front__yourself">Yourself...</span>
    </h1>
    <div class="front__photo" role="img" aria-label="Photo of a kung fu practitioner in a low wide stance with arms extended"></div>
    <p class="front__pitch">Teaching is the highest form of learning. Be a part of a professional, dedicated team, delivering the highest level Kung Fu...</p>
    <div class="front__seal" aria-hidden="true"></div>
    <p class="front__brand">Copper Wren Martial Arts</p>
  </section>

  <section class="flyer flyer--back" aria-label="Flyer back">
    <svg class="back__bands" width="472" height="664" viewBox="0 0 472 664" aria-hidden="true">
      <defs>
        <linearGradient id="band-dark" x1="0" y1="0" x2="1" y2="0">
          <stop offset="0" stop-color="#2f2828"/>
          <stop offset="0.5" stop-color="#443c3c"/>
          <stop offset="1" stop-color="#2f2828"/>
        </linearGradient>
        <radialGradient id="band-red" cx="0.5" cy="0.5" r="0.7">
          <stop offset="0" stop-color="#e8252f"/>
          <stop offset="1" stop-color="#d81d27"/>
        </radialGradient>
      </defs>
      <rect x="0" y="0" width="472" height="664" fill="#ececec"/>
      <polygon points="0,0 472,0 472,92 0,140" fill="url(#band-dark)"/>
      <polygon points="0,140 472,92 472,104 0,152" fill="#ffffff"/>
      <polygon points="0,152 472,104 472,524 0,571" fill="url(#band-red)"/>
    </svg>

    <h2 class="back__title">Seeking martial arts<br>instructors!</h2>

    <div class="back__copy">
      <p>We train in one of the world's most effective martial art systems, Choy Li Fut Kung Fu. As an instructor, you will teach both beginner and intermediate level Kung Fu skills to adults and children at Copper Wren Martial Arts, Brisbane's premier martial arts school.</p>
      <p>As an instructor, you will:</p>
      <ul class="duties">
        <li>Teach fundamentals to children and adults of all ages and abilities</li>
        <li>Progress student's martial arts and life skills</li>
        <li>Deliver fun and engaging classes</li>
        <li>Develop and grow your martial arts skills at an advanced level and pace</li>
      </ul>
      <p>In return, you will receive your training tuition, which includes our high level instructor training program, until qualified and then a weekly one one on one with our very own Sifu, as well as one hour training sessions, twice a week , with our team.</p>
    </div>

    <div class="back__contact">
      <p class="back__contact-note">To discuss your interest and<br>suitability - ask for Sifu Rory.<br>Contact us on:</p>
      <p class="back__phone">0491 570 183</p>
    </div>

    <div class="back__brand">
      <p class="back__brand-name">Copper Wren<br>Martial Arts</p>
      <p class="back__motto">"Challenge yourself... for life!</p>
    </div>
    <div class="back__seal" aria-hidden="true"></div>
  </section>

</main>
</body>
</html>
```